Business Card Design and Logo Needed

I need Business Cards and a Logo for my website and public speaking business which can be found at: www.corvina-lett.example

I'm looking for creative and unique ideas. Some business cards I've found online that I like can be found at:
http://gigbarrow.example/general/18-smokin-hot-business-card-designs/

and at

http://www.plumquarry.example/2009/04/50-creative-business-cards-of-50-graphic-designers/

```html
<!DOCTYPE html>
<html lang="en">
<head>
<meta charset="utf-8">
<title>Corvina Lett — Business Card</title>
<link rel="stylesheet" href="https://fonts.googleapis.com/css2?family=Michroma&display=swap">
<style>
  :root {
    --page-bg: #ffffff;
    --card-top: #5e1a10;
    --card-mid: #6e2216;
    --card-bottom: #7c2c1c;
    --role-red: #c4323a;
    --contact-light: #ecd2ca;
    --badge-fill: rgba(255, 255, 255, 0.22);
    --badge-text: #f3dcd4;
  }
  html, body {
    margin: 0;
    padding: 0;
    width: 1200px;
    height: 896px;
    overflow: hidden;
    background: var(--page-bg);
  }
  .canvas {
    position: relative;
    width: 1200px;
    height: 896px;
  }
  .card {
    position: absolute;
    left: 31px;
    top: 86px;
    width: 1164px;
    height: 728px;
    border-radius: 0 130px 0 155px;
    overflow: hidden;
    font-family: "Michroma", sans-serif;
  }
  .card-texture {
    position: absolute;
    inset: 0;
    background: linear-gradient(160deg, var(--card-top) 0%, var(--card-mid) 50%, var(--card-bottom) 100%);
  }
  .brand-badge {
    position: absolute;
    left: 862px;
    top: 64px;
    width: 236px;
    height: 236px;
    border-radius: 50%;
    background: var(--badge-fill);
    display: flex;
    align-items: center;
    justify-content: center;
  }
  .brand-name {
    color: var(--badge-text);
    font-size: 17px;
    letter-spacing: 2px;
    text-align: center;
    line-height: 1.5;
    text-transform: uppercase;
  }
  .roles,
  .contact {
    position: absolute;
    top: 460px;
    margin: 0;
    padding: 0;
    list-style: none;
    font-size: 24px;
    letter-spacing: 2px;
    line-height: 64px;
    text-transform: uppercase;
    white-space: nowrap;
  }
  .roles {
    left: 63px;
    color: var(--role-red);
  }
  .contact {
    right: 65px;
    text-align: right;
    color: var(--contact-light);
  }
</style>
</head>
<body>
<div class="canvas">
  <section class="card">
    <div class="card-texture" role="img" aria-label="Dark red checkered texture background"></div>
    <div class="brand-badge">
      <span class="brand-name">Corvina<br>Lett</span>
    </div>
    <ul class="roles">
      <li>Motivational Speaker</li>
      <li>Philanthropist</li>
      <li>Author</li>
    </ul>
    <ul class="contact">
      <li>Mob : 0147 258036</li>
      <li>www.corvina-lett.example</li>
      <li>hello@corvina-lett.example</li>
    </ul>
  </section>
</div>
</body>
</html>
```